We need a laundry sheet packingbox desgin

-look at our website lindavel.nl to be in line with our house style/collor
We are a perfume seller and would like to offer also wasshingsheets with NO SMELL, so the customers can buy this incombination with our washingperfumes.
-the wassingheets will be neutrale(NO SMELL)
-it will be for the Dutch market
The next points should be on the desgin of the package
-our brand name: LINDAVEL
-product name: WASSTRIPS
-(contains) Bevat: 30 wasstrips
-30 wasstrips = 60 wasbeurten
Please take some inspiration of others sellers & regarding eco friendly symbols etc.:
voltirra.com & plomkens.nl
Backside information will be provided afther we found the right desgin
Please look at attachement pdf open box.
Here you can find the pdf design where you need to customize:
https://fz.qx/t-kR8bNwL2sY

```html
<!DOCTYPE html>
<html lang="nl">
<head>
<meta charset="utf-8">
<title>LINDAVEL Wasstrips – doosontwerp</title>
<link rel="stylesheet" href="https://fonts.googleapis.com/css2?family=Montserrat:wght@400;500;600&family=Marcellus&display=swap">
<style>
  :root {
    --ink: #000000;
    --gold: #cc973a;
    --gold-soft: #d9a843;
    --white: #ffffff;
    --cut: #6cc04a;
    --fold: #c0392b;
    --window: #3f8fa0;
    --perf: #e53935;
    --strip: #cfcfcf;
    --frame: #4a4a4a;
  }
  html, body { margin: 0; padding: 0; background: var(--ink); overflow: hidden; }
  .canvas { display: block; width: 1200px; height: 974px; }
  .board-frame { fill: var(--ink); stroke: var(--frame); stroke-width: 5; }
  .cut { fill: none; stroke: var(--cut); stroke-width: 1.6; }
  .fold { fill: none; stroke: var(--fold); stroke-width: 1.4; }
  .panel-gold { fill: var(--gold); }
  .glue-strip { fill: var(--strip); }
  .perforation { stroke: var(--perf); stroke-width: 2; stroke-dasharray: 9 9; }
  .window-cut { fill: none; stroke: var(--window); stroke-width: 1.6; }
  .window-perf { fill: none; stroke: var(--perf); stroke-width: 2; stroke-dasharray: 10 7; }
  .brand { font-family: "Marcellus", serif; }
  .brand-gold { fill: var(--gold-soft); }
  .brand-dark { fill: var(--ink); }
  .product-title { font-family: "Montserrat", sans-serif; font-weight: 500; font-size: 64px; fill: var(--white); }
  .icon-ring { fill: none; stroke: var(--gold); stroke-width: 2.5; }
  .icon-label { font-family: "Montserrat", sans-serif; font-size: 10px; fill: var(--white); }
  .pill-text { font-family: "Montserrat", sans-serif; font-weight: 500; font-size: 20px; }
  .tag-text { font-family: "Montserrat", sans-serif; font-weight: 500; font-size: 7px; fill: var(--ink); }
</style>
</head>
<body>
<svg class="canvas" viewBox="0 0 2139 1736" width="1200" height="974" xmlns="http://www.w3.org/2000/svg">
  <defs>
    <linearGradient id="machine-tone" x1="0" y1="0" x2="1" y2="1">
      <stop offset="0" stop-color="#cc973a" stop-opacity="0.55"/>
      <stop offset="1" stop-color="#cc973a" stop-opacity="0.15"/>
    </linearGradient>
    <radialGradient id="halftone-tone" cx="0.6" cy="0.45" r="0.6">
      <stop offset="0" stop-color="#2a2a2a"/>
      <stop offset="1" stop-color="#000000"/>
    </radialGradient>
  </defs>

  <rect class="board-frame" x="2" y="2" width="2135" height="1732"/>

  <!-- Gold panels -->
  <rect class="panel-gold" x="1004" y="474" width="129" height="788"/>
  <path class="panel-gold" d="M1713,474 L1800,474 Q1838,474 1838,512 L1838,1224 Q1838,1262 1800,1262 L1713,1262 Z"/>

  <!-- Glue strips on dust flaps -->
  <g class="glue-zone">
    <rect class="glue-strip" x="456" y="381" width="516" height="71"/>
    <rect class="glue-strip" x="460" y="1291" width="516" height="61"/>
    <g class="perforation">
      <path d="M469,385V448 M507,385V448 M545,385V448 M583,385V448 M621,385V448 M659,385V448 M697,385V448 M735,385V448 M773,385V448 M811,385V448 M849,385V448 M887,385V448 M925,385V448 M962,385V448"/>
      <path d="M473,1295V1348 M511,1295V1348 M549,1295V1348 M587,1295V1348 M625,1295V1348 M663,1295V1348 M701,1295V1348 M739,1295V1348 M777,1295V1348 M815,1295V1348 M853,1295V1348 M891,1295V1348 M929,1295V1348 M966,1295V1348"/>
    </g>
  </g>

  <!-- Fold lines -->
  <g class="fold">
    <rect x="300" y="474" width="126" height="788"/>
    <rect x="426" y="470" width="578" height="796"/>
    <rect x="1004" y="474" width="129" height="788"/>
    <rect x="1133" y="470" width="580" height="796"/>
    <path d="M1805,660 V1085"/>
  </g>

  <!-- Cut lines -->
  <g class="cut">
    <path d="M300,474 L310,362 Q311,355 318,355 L403,355 Q410,355 411,362 L420,470 Q422,474 426,474"/>
    <path d="M300,1262 L310,1374 Q311,1382 318,1382 L403,1382 Q410,1382 411,1374 L420,1266 Q422,1262 426,1262"/>
    <path d="M300,474 V1262"/>
    <path d="M426,474 Q430,470 431,465 L437,362 Q438,355 446,355 L982,355 Q990,355 991,362 L998,465 Q1000,474 1008,470"/>
    <path d="M426,1262 Q430,1266 431,1271 L437,1374 Q438,1382 446,1382 L982,1382 Q990,1382 991,1374 L998,1271 Q1000,1262 1008,1266"/>
    <path d="M1008,470 L1020,362 Q1021,355 1028,355 L1110,355 Q1117,355 1118,362 L1128,465 Q1130,474 1138,470"/>
    <path d="M1008,1266 L1020,1374 Q1021,1382 1028,1382 L1110,1382 Q1117,1382 1118,1374 L1128,1271 Q1130,1262 1138,1266"/>
    <path d="M1138,470 L1143,353 Q1144,345 1152,345 L1692,345 Q1700,345 1701,353 L1709,468 Q1711,474 1713,474"/>
    <path d="M1138,1266 L1143,1382 Q1144,1390 1152,1390 L1692,1390 Q1700,1390 1701,1382 L1709,1268 Q1711,1262 1713,1262"/>
    <path d="M1713,474 L1800,474 Q1838,474 1838,512 L1838,1224 Q1838,1262 1800,1262 L1713,1262"/>
    <path d="M382,818 L396,828 L396,908 L382,918 Z"/>
    <path d="M1805,835 A35,35 0 0 0 1805,902"/>
  </g>

  <!-- Spine branding -->
  <g class="spine-brand">
    <circle cx="1068" cy="808" r="9" fill="none" stroke="#000" stroke-width="2.5"/>
    <text class="brand brand-dark" font-size="18" textLength="102" lengthAdjust="spacingAndGlyphs" transform="translate(1062,836) rotate(90)">LINDAVEL</text>
  </g>

  <!-- Front panel -->
  <g class="front-panel">
    <rect x="1490" y="470" width="223" height="290" fill="url(#halftone-tone)" role="img" aria-label="Halftone dot pattern fading from the top right corner"/>
    <rect x="1305" y="470" width="238" height="138" rx="14" fill="url(#machine-tone)" role="img" aria-label="Gold line illustration of a front-loading washing machine"/>

    <g class="window-die">
      <path class="window-cut" d="M1805,660 L1788,600 Q1775,569 1745,569 L1230,569 Q1219,569 1219,580 L1219,1155 Q1219,1166 1230,1166 L1745,1166 Q1775,1166 1788,1136 L1805,1085"/>
      <path class="window-perf" d="M1268,575 L1750,575 Q1772,575 1782,600 L1800,660 M1800,1085 L1782,1134 Q1772,1160 1750,1160 L1268,1160"/>
    </g>

    <g class="front-brand">
      <circle cx="1305" cy="858" r="34" fill="none" stroke="var(--gold-soft)" stroke-width="4"/>
      <text class="brand brand-gold" font-size="16" textLength="98" lengthAdjust="spacingAndGlyphs" transform="translate(1366,907) rotate(-90)">LINDAVEL</text>
    </g>

    <text class="product-title" textLength="362" lengthAdjust="spacingAndGlyphs" transform="translate(1435,1100) rotate(-90)">WASSTRIPS</text>

    <g class="sheet-badge">
      <circle cx="1413" cy="678" r="44" fill="var(--white)"/>
      <rect x="1390" y="655" width="34" height="44" rx="3" fill="none" stroke="#000" stroke-width="6" transform="rotate(-20 1407 677)"/>
      <rect x="1404" y="661" width="34" height="40" rx="3" fill="#000" transform="rotate(-12 1421 681)"/>
    </g>

    <g class="feature neutral">
      <circle class="icon-ring" cx="1534" cy="821" r="28"/>
      <path d="M1522,812 q6,-6 12,0 t12,0 M1522,822 q6,-6 12,0 t12,0 M1522,832 q6,-6 12,0 t12,0" fill="none" stroke="var(--gold)" stroke-width="2"/>
      <text class="icon-label" text-anchor="middle" transform="translate(1575,821) rotate(-90)">Neutrale</text>
      <text class="icon-label" text-anchor="middle" transform="translate(1587,821) rotate(-90)">(Geen Geur)</text>
    </g>
    <circle cx="1531" cy="867" r="2" fill="var(--gold)"/>
    <g class="feature all-fabrics">
      <circle class="icon-ring" cx="1534" cy="913" r="28"/>
      <rect x="1522" y="902" width="22" height="22" rx="2" fill="none" stroke="var(--gold)" stroke-width="2"/>
      <text class="icon-label" text-anchor="middle" transform="translate(1575,915) rotate(-90)">Voor alle</text>
      <text class="icon-label" text-anchor="middle" transform="translate(1587,915) rotate(-90)">kledingtypes</text>
    </g>

    <g class="contents-pill">
      <rect x="1640" y="770" width="13" height="195" rx="3" fill="var(--white)"/>
      <text class="tag-text" text-anchor="middle" textLength="160" lengthAdjust="spacingAndGlyphs" transform="translate(1649,867) rotate(-90)">30 WASSTRIPS = 60 WASBEURTEN</text>
      <rect x="1612" y="755" width="28" height="225" rx="14" fill="var(--gold)"/>
      <rect x="1615" y="895" width="22" height="82" rx="11" fill="var(--ink)"/>
      <text class="pill-text" fill="var(--gold)" text-anchor="middle" textLength="62" lengthAdjust="spacingAndGlyphs" transform="translate(1633,936) rotate(-90)">Bevat</text>
      <text class="pill-text" fill="var(--ink)" text-anchor="middle" textLength="118" lengthAdjust="spacingAndGlyphs" transform="translate(1633,826) rotate(-90)">30 wasstrips</text>
    </g>
  </g>

  <!-- Tuck flap branding -->
  <g class="tuck-brand">
    <circle cx="1768" cy="928" r="9" fill="none" stroke="#000" stroke-width="2.5"/>
    <text class="brand brand-dark" font-size="18" textLength="102" lengthAdjust="spacingAndGlyphs" transform="translate(1775,903) rotate(-90)">LINDAVEL</text>
  </g>
</svg>
</body>
</html>
```